Medical consulting firm needs polished website

I am a physician and working on setting up a smal consulting firm in New Hampshire, USA. It is called Bright Harbor Medical Services, LLC and the website will be BrightHarborMed.com. I was puttering around at making my own website, and it just didn't come together nicely so I've decided to leave it to the pros. The focus of the business is Advanced Care Planning, ie planning for your future medical needs. So it deals with some heavy stuff like planning for if you get sick, who should make decisions for you, end of life options etc. So it can't be too flippant or cutesy, but also can't be too dour and dark. I am hoping to convey that by thinking ahead and making some plans you can lift some of the worries off of yourself and your family - and that we can help make a scary sounding path more manageable. I want it to be made with wordpress and I have actually already bought a template ( Vitarun – A Modern Multidisciplinary Medical & Health Theme ). The website needs to have general information about our services, doc profile, appointment maker, blog/url link page, and ideally web commerce application ( the template has access to woocommerce). I've posted my business card and current brochure (still tweaking them, but you get the idea). I am also partnering with lumenfold.com and so have included their logo and would want connections/info about them. I have the logos etc in different formats as needed.

Target Market(s)

middle aged to older adults

Industry/Entity Type

Medical

Coding

Coded - Design and coding required

Font styles to use
Sans Serif

Requirements
Must have
• as above.
Nice to have
• Ease of reading/access for elderly viewers. woo commerce.

```html
<!DOCTYPE html>
<html lang="en">
<head>
<meta charset="utf-8">
<title>Bright Harbor Medical Services – Advanced Care Planning</title>
<link rel="stylesheet" href="https://fonts.googleapis.com/css2?family=Open+Sans:wght@300;400;600;700&display=swap">
<style>
:root{
  --blue:#1f6db4;
  --blue-dark:#1a5fa0;
  --sky:#3b8fd6;
  --green:#3fa33f;
  --ink:#333;
  --muted:#8a8a8a;
  --line:#e4e4e4;
  --page:#f4f4f4;
  --footer:#efefef;
  --white:#fff;
}
*{box-sizing:border-box;margin:0;padding:0}
html,body{width:1200px;height:3352px;overflow:hidden}
body{font-family:"Open Sans",Arial,sans-serif;color:var(--ink);background:var(--page);position:relative}
.wrap{width:934px;margin:0 auto;position:relative}

/* header */
.topbar{height:134px;background:var(--white);border-bottom:1px solid var(--line)}
.brand{position:absolute;left:0;top:34px;display:flex;align-items:center;gap:12px}
.brand-dot{width:64px;height:64px;border-radius:50%;background:var(--blue)}
.brand-name{font-size:25px;font-weight:600;color:var(--blue);line-height:1.12;width:230px}
.contact-item{position:absolute;top:46px;display:flex;align-items:center;gap:12px}
.contact-item small{display:block;font-size:13px;color:var(--muted)}
.contact-item strong{display:block;font-size:18px;font-weight:600;color:#222}
.navbar{height:56px;background:var(--white);border-bottom:1px solid var(--line)}
.nav{display:flex;gap:34px;height:56px;align-items:center;font-size:12px;font-weight:600;text-transform:uppercase;color:#555}
.nav .active{color:var(--blue)}
.search{position:absolute;right:148px;top:16px}
.quick{position:absolute;right:0;top:0;width:134px;height:56px;background:var(--blue);color:#fff;font-size:12px;font-weight:600;display:flex;align-items:center;justify-content:center}

/* hero */
.hero{height:358px;position:relative;overflow:hidden}
.hero-photo{position:absolute;inset:0;
  background:
    radial-gradient(circle at 78% 52%,#fbfaf6 0%,#f3f0ea 34%,rgba(236,232,225,0) 60%),
    linear-gradient(90deg,#cfdbe2 0%,#e4e6e4 12%,#c9b6a6 24%,#f6f4f1 33%,#efe9e2 42%,#e2ddd5 55%,#ece8e1 100%)}
.hero-title{position:absolute;right:132px;top:126px;text-align:right;font-size:40px;font-weight:300;color:#444;line-height:1.22}
.btn-green{position:absolute;right:132px;top:240px;background:var(--green);color:#fff;font-size:14px;font-weight:600;padding:12px 24px}
.arrow{position:absolute;top:166px}

/* welcome */
.welcome{position:absolute;left:133px;top:568px;width:934px;height:174px;background:#fff;text-align:center;padding:28px 34px}
.section-title{font-size:28px;font-weight:700;text-transform:uppercase;text-align:center}
.welcome h2{color:var(--green);font-size:28px;font-weight:700;margin-bottom:10px;line-height:1.2}
.welcome p{font-size:11.5px;line-height:1.75;color:#666}

/* services */
.services-title{position:absolute;top:802px;left:0;width:1200px;color:var(--blue)}
.card{position:absolute;width:297px;height:280px;background:#fff}
.card .ph{height:199px}
.card p{font-size:13px;line-height:1.5;text-align:center;padding:20px 40px 0;color:#333}

/* tweet */
.tweet{position:absolute;left:0;top:1520px;width:1200px;height:199px;background:var(--sky);color:#fff;text-align:center}
.tweet .dot{width:26px;height:26px;border-radius:50%;background:#fff;margin:52px auto 14px}
.tweet p{font-size:21px}
.tweet small{display:block;font-size:14px;margin-top:8px}

/* about */
.about{position:absolute;left:0;top:1719px;width:1200px;height:400px;background:#fff}
.about-photo{position:absolute;left:0;top:0;width:599px;height:400px;
  background:
    radial-gradient(ellipse 38% 70% at 52% 62%,#f7f9fb 0%,#eef3f7 55%,rgba(238,243,247,0) 75%),
    linear-gradient(90deg,#8fb9dc 0%,#b7d3ea 30%,#dbe8f3 60%,#f3f6f9 100%)}
.about-text{position:absolute;left:630px;top:50px;width:436px}
.about-text h2{font-size:28px;font-weight:700;color:var(--green);margin-bottom:14px;line-height:1.2}
.about-text p{font-size:11px;line-height:1.85;color:#777;text-align:justify;margin-bottom:18px}

/* blog */
.blog-title{position:absolute;top:2182px;left:0;width:1200px;color:var(--blue)}
.post{position:absolute;top:2244px;width:297px;height:326px;background:#fff}
.post .ph{height:168px}
.post h3{font-size:13px;font-weight:400;line-height:1.5;color:#222;padding:20px 22px 8px}
.post p{font-size:10px;line-height:1.6;color:#999;padding:0 22px}
.post a{display:block;font-size:10px;font-weight:600;color:var(--blue);text-decoration:none;text-transform:uppercase;padding:12px 22px}

/* newsletter */
.newsletter{position:absolute;left:0;top:2655px;width:1200px;height:268px;background:#fff;border-bottom:1px solid var(--line);text-align:center}
.newsletter h2{font-size:28px;font-weight:700;color:var(--blue);margin-top:66px;text-transform:uppercase;line-height:1.2}
.newsletter .sub{font-size:16px;color:#444;margin-top:2px}
.form{display:flex;justify-content:center;gap:22px;margin-top:28px}
.field{width:282px;height:44px;border:1px solid #ddd;background:#f7f7f7;font-size:12px;color:#888;text-align:left;padding:13px 20px}
.subscribe{width:112px;height:44px;background:var(--blue);color:#fff;font-size:12px;font-weight:600;padding-top:14px;text-transform:uppercase}

/* partner */
.partner{position:absolute;left:0;top:2923px;width:1200px;height:145px;background:#fff}
.partner-mark{position:absolute;left:240px;top:50px;display:flex;align-items:center;gap:12px}
.partner-mark span{width:40px;height:40px;border-radius:50%;background:var(--blue-dark);display:block}
.partner-mark b{font-size:40px;font-weight:400;color:var(--blue-dark);line-height:1}
.partner p{position:absolute;left:527px;top:42px;width:440px;font-size:11px;line-height:1.75;color:#888}

/* footer */
.footer{position:absolute;left:0;top:3068px;width:1200px;height:229px;background:var(--footer)}
.f-brand{position:absolute;left:133px;top:36px;display:flex;align-items:center;gap:10px}
.f-brand span{width:52px;height:52px;border-radius:50%;background:#aaa;display:block}
.f-brand b{font-size:22px;font-weight:600;color:#999;width:210px;line-height:1.1}
.f-desc{position:absolute;left:133px;top:124px;width:250px;font-size:10px;line-height:1.6;color:#888}
.f-col h4{font-size:12.5px;font-weight:600;text-transform:uppercase;color:#333;margin-bottom:20px}
.f-contact{position:absolute;left:456px;top:36px}
.f-contact ul{list-style:none}
.f-contact li{display:flex;align-items:center;gap:12px;font-size:11px;color:#777;margin-bottom:14px}
.social{display:flex;gap:16px;margin-top:6px}
.social i{width:14px;height:14px;border-radius:50%;background:#999;display:block}
.f-links{position:absolute;left:836px;top:36px}
.f-links ul{list-style:none;display:grid;grid-template-columns:108px 120px;row-gap:14px;font-size:11px;color:#777}
.copy{position:absolute;left:0;top:3297px;width:1200px;height:55px;background:#fff}
.copy p{position:absolute;left:133px;top:20px;font-size:11px;color:#888}
.totop{position:absolute;right:132px;top:12px;width:30px;height:30px}
</style>
</head>
<body>

<header class="topbar">
  <div class="wrap">
    <div class="brand"><span class="brand-dot"></span><span class="brand-name">Bright Harbor Medical Services</span></div>
    <div class="contact-item" style="left:444px">
      <svg width="24" height="38" viewBox="0 0 24 38" fill="none" stroke="#555" stroke-width="2"><rect x="2" y="2" width="20" height="34" rx="3"/><line x1="9" y1="31" x2="15" y2="31"/></svg>
      <div><small>Call us on</small><strong>603-555-0142</strong></div>
    </div>
    <div class="contact-item" style="left:664px">
      <svg width="40" height="30" viewBox="0 0 40 30" fill="none" stroke="#555" stroke-width="2"><rect x="2" y="2" width="36" height="26"/><polyline points="2,2 20,17 38,2"/></svg>
      <div><small>Email</small><strong>info@brightharbormed.com</strong></div>
    </div>
  </div>
</header>

<nav class="navbar">
  <div class="wrap">
    <div class="nav"><span class="active">Home</span><span>About Us</span><span>Services</span><span>Blog</span><span>Contact Us</span></div>
    <svg class="search" width="26" height="26" viewBox="0 0 26 26" fill="none" stroke="#aaa" stroke-width="2"><circle cx="11" cy="11" r="8"/><line x1="17" y1="17" x2="24" y2="24"/></svg>
    <div class="quick">QUICK CONTACT</div>
  </div>
</nav>

<section class="hero">
  <div class="hero-photo" role="img" aria-label="Photo of a woman in a white t-shirt holding her stomach in a bright room"></div>
  <h1 class="hero-title">Advanced Care<br>Planning Specialists</h1>
  <div class="btn-green">Get Started now</div>
  <svg class="arrow" style="left:22px" width="14" height="26" viewBox="0 0 14 26" fill="none" stroke="#888" stroke-width="2"><polyline points="12,2 2,13 12,24"/></svg>
  <svg class="arrow" style="right:22px" width="14" height="26" viewBox="0 0 14 26" fill="none" stroke="#888" stroke-width="2"><polyline points="2,2 12,13 2,24"/></svg>
</section>

<section class="welcome">
  <h2>WELCOME</h2>
  <p>Advanced Directives are legally binding documents that spell out what type of medical care you would - or would not - want done to you. We often assume that our families or medical professionals will make "the right decision", but this can be an anguishing process - and often does not accurately reflects the patient's true desires. By making your choices clear, your family and caregivers can honor your wishes when you cannot speak for yourself.</p>
</section>

<h2 class="section-title services-title">Our Services Include</h2>
<article class="card" style="left:132px;top:860px"><div class="ph" role="img" aria-label="Photo of a doctor consulting a patient at a desk" style="background:linear-gradient(100deg,#aecde2 0%,#e6eff5 35%,#dfe7ec 55%,#5a6470 75%,#c7d8e3 100%)"></div><p>Individualized physician-guided healthcare planning</p></article>
<article class="card" style="left:451px;top:860px"><div class="ph" role="img" aria-label="Photo of a patient in a medical scanner room" style="background:linear-gradient(120deg,#e9eef1 0%,#c4d6e2 30%,#8fb3cc 55%,#d7e3ea 80%,#eef2f4 100%)"></div><p>Helping navigate complex medical situations</p></article>
<article class="card" style="left:771px;top:860px"><div class="ph" role="img" aria-label="Photo of a doctor shaking hands with a man" style="background:linear-gradient(95deg,#eef1f3 0%,#f6f7f8 35%,#d9dee2 55%,#3b4049 80%,#2f333a 100%)"></div><p>Creating legally binding Advanced Directives</p></article>
<article class="card" style="left:293px;top:1162px"><div class="ph" role="img" aria-label="Photo of a nurse comforting an elderly woman" style="background:linear-gradient(110deg,#f3efe9 0%,#e9dfd3 35%,#f1ece5 55%,#a9cfe3 80%,#cfe3ee 100%)"></div><p>Sharing your decisions with your loved ones and your doctor</p></article>
<article class="card" style="left:612px;top:1162px"><div class="ph" role="img" aria-label="Photo of a nurse working at a computer" style="background:linear-gradient(100deg,#d3e2ec 0%,#7fa6c4 30%,#b8cfdf 50%,#eef2f5 75%,#f7f8f9 100%)"></div><p>Secure, accessible, web-based storage of your documents</p></article>

<section class="tweet">
  <div class="dot"></div>
  <p>Aenean sit amet tincidunt enim, eu volutpat eros aliquet dignissim malesuada</p>
  <small>@brightharbormed</small>
</section>

<section class="about">
  <div class="about-photo" role="img" aria-label="Photo of a smiling female doctor with a stethoscope"></div>
  <div class="about-text">
    <h2>ABOUT US</h2>
    <p>Phasellus venenatis a odio eu vestibulum. Proin a est ac odio porttitor posuere. Pellentesque eget luctus lectus. Aliquam egestas elementum risus. Nunc convallis nisi dolor. In cursus justo placerat ac. Duis tellus risus, viverra vel ex id, consectetur vulputate lectus. Proin enim nunc, gravida eget odio facilisis.</p>
    <p>Curabitur ut congue arcu. Sed finibus quis erat quis elementum. Vivamus facilisis quis sapien ut condimentum. Sed lobortis congue diam fermentum tincidunt. Aenean sit amet tincidunt enim, eu volutpat eros. Sed mi nisl, aliquet dignissim malesuada vitae, volutpat convallis nisl. Phasellus et blandit erat. Cras sed fermentum mauris. Sed a eros vitae ante blandit facilisis. Cras eu arcu rutrum, tincidunt purus et, lacinia eros. Nam sagittis purus id dui hendrerit, efficitur dignissim dolor ornare. Duis laoreet sed augue non interdum. Praesent gravida, turpis ac placerat ornare, ante justo mattis quam, a viverra urna ligula imperdiet neque.</p>
  </div>
</section>

<h2 class="section-title blog-title">Blog</h2>
<article class="post" style="left:132px"><div class="ph" role="img" aria-label="Photo of a girl testing her blood sugar" style="background:linear-gradient(100deg,#4f95d1 0%,#8fbde3 30%,#f0dccb 55%,#e9c8ad 75%,#6fa9d8 100%)"></div><h3>Aenean sed quam non sapien faucibus con sequat vitae sit amet orci</h3><p>Proin porta fermentum ipsum, vel porttitor turpis viverra eu luctus. Vivamus volutpat eu sapien quis tempus. Aenean feugiat viverra lorem ac sagittis.</p><a href="#">Read more</a></article>
<article class="post" style="left:451px"><div class="ph" role="img" aria-label="Photo of a man holding his chest" style="background:linear-gradient(100deg,#dfe6ee 0%,#b7c9dc 30%,#7f9dc0 50%,#b9cadb 70%,#e4eaf0 100%)"></div><h3>Aenean sed quam non sapien faucibus con sequat vitae sit amet orci</h3><p>Proin porta fermentum ipsum, vel porttitor turpis viverra eu luctus. Vivamus volutpat eu sapien quis tempus. Aenean feugiat viverra lorem ac sagittis.</p><a href="#">Read more</a></article>
<article class="post" style="left:771px"><div class="ph" role="img" aria-label="Photo of a pharmacist in a pharmacy" style="background:linear-gradient(100deg,#cfe0cf 0%,#e7eee4 30%,#f3ede6 50%,#c79a7a 65%,#f2f0ec 85%,#dfe9dc 100%)"></div><h3>Aenean sed quam non sapien faucibus con sequat vitae sit amet orci</h3><p>Proin porta fermentum ipsum, vel porttitor turpis viverra eu luctus. Vivamus volutpat eu sapien quis tempus. Aenean feugiat viverra lorem ac sagittis.</p><a href="#">Read more</a></article>

<section class="newsletter">
  <h2>Newsletter Subscribe</h2>
  <p class="sub">Donec luctus lacus quis risus mollis, vel tempor nisl lacini</p>
  <div class="form"><div class="field">Name</div><div class="field">Email</div><div class="subscribe">Subscribe</div></div>
</section>

<section class="partner">
  <div class="partner-mark"><span></span><b>lumenfold</b></div>
  <p>Donec at magna nec dolor vulputate scelerisque id et dolor. Ut efficitur tellus vel lorem tempus, eget sagittis dui faucibus. Vestibulum vestibulum tempus odio, id bibendum ligula ornare semper.</p>
</section>

<footer class="footer">
  <div class="f-brand"><span></span><b>Bright Harbor Medical Services</b></div>
  <p class="f-desc">Donec at magna nec dolor vulputate scelerisque id et dolor. Ut efficitur tellus vel lorem tempus, eget sagittis dui faucibus. Vestibulum vestibulum tempus odio.</p>
  <div class="f-col f-contact">
    <h4>Contact Info</h4>
    <ul>
      <li><svg width="10" height="14" viewBox="0 0 10 14"><path d="M5 0a5 5 0 0 0-5 5c0 4 5 9 5 9s5-5 5-9a5 5 0 0 0-5-5zm0 7a2 2 0 1 1 0-4 2 2 0 0 1 0 4z" fill="#777"/></svg>24 Building name, Street name, City - Zipcode</li>
      <li><svg width="10" height="14" viewBox="0 0 10 14"><rect x="1" y="1" width="8" height="12" rx="1.5" fill="none" stroke="#777" stroke-width="1.5"/></svg>Call us on : 603 - 555 - 0142</li>
      <li><svg width="12" height="10" viewBox="0 0 12 10" fill="none" stroke="#777" stroke-width="1.3"><rect x="0.7" y="0.7" width="10.6" height="8.6"/><polyline points="0.7,0.7 6,5.5 11.3,0.7"/></svg>Email : info@brightharbormed.com</li>
    </ul>
    <div class="social"><i></i><i></i><i></i><i></i><i></i></div>
  </div>
  <div class="f-col f-links">
    <h4>Links</h4>
    <ul><li>Home</li><li>Contact Us</li><li>About Us</li><li>Terms and Conditions</li><li>Services</li><li>Privacy Policy</li><li>Blog</li><li>Sitemap</li></ul>
  </div>
</footer>

<div class="copy">
  <p>Copyright © 2016 Company name. All rights reserved.</p>
  <svg class="totop" viewBox="0 0 30 30"><circle cx="15" cy="15" r="15" fill="#ccc"/><polyline points="9,18 15,11 21,18" fill="none" stroke="#fff" stroke-width="2.5"/></svg>
</div>

</body>
</html>
```